Website for "Bright Morrow Ltd" cleaning bsuiness

We require a website to expose our business to the local market. We want to provide background on who we are and what we do but in an easily digestible way. We clean domestic and commercial premises and want to provide a list of all of our services to potential customers. We operate out of Warrington in the UK.

We would like the website to be animated in some way so that the experience of using it is not dull or mundane. This website needs to be an extension of our company.

Target Market(s)

30 - 60 year olds for Domestic plus commercial clients

Industry/Entity Type

Cleaning Service

Coding

Coded - Design and coding required

Number of Pages Required

4 page

Font styles to use
Sans Serif

Colors
0455a3
3176b5
85acd3
cfdeed
ffffff
000000
1b1b1b
c8c8c8
757575

Requirements
Must have
• Logo which has been provided. Theme based around the logo and its colours. Simple layout to avoid confusion.
Nice to have
• Animations where possible to impress the customer.
Should not have
• any pictures of cleaning equipment, fairies, maids etc

```html
<!DOCTYPE html>
<html lang="en">
<head>
<meta charset="utf-8">
<title>Bright Morrow Ltd – Domestic and Commercial Cleaning</title>
<link href="https://fonts.googleapis.com/css2?family=Open+Sans:ital,wght@0,400;0,600;1,400&family=Roboto:wght@300;400;500&display=swap" rel="stylesheet">
<style>
:root{
  --brand-deep:#0455a3;
  --brand:#3176b5;
  --brand-soft:#85acd3;
  --brand-pale:#cfdeed;
  --white:#ffffff;
  --black:#000000;
  --ink:#1b1b1b;
  --line:#c8c8c8;
  --muted:#757575;
  --star:#f5a623;
  --placeholder-a:#eceae6;
  --placeholder-b:#d9d4cc;
  --tile-a:#eef0f2;
  --tile-b:#d5dadf;
}
*{margin:0;padding:0;box-sizing:border-box}
html,body{width:1200px;height:2510px;overflow:hidden;background:var(--white)}
body{position:relative;font-family:"Open Sans",Arial,sans-serif;color:var(--ink)}
.abs{position:absolute}
.head-font{font-family:"Roboto",Arial,sans-serif}

/* header */
.site-header{left:0;top:0;width:1200px;height:122px;background:var(--white)}
.brand{left:135px;top:28px;display:flex;align-items:center;gap:12px}
.brand-dot{width:46px;height:46px;border-radius:50%;background:var(--brand-deep)}
.brand-name{font-family:"Roboto",Arial,sans-serif;font-weight:500;font-size:25px;line-height:1.1;color:var(--brand-deep);width:150px}
.phone{right:115px;top:24px;display:flex;align-items:center;gap:8px;font-family:"Roboto",Arial,sans-serif;font-size:22px;color:var(--brand-deep)}
.main-nav{left:398px;top:70px;display:flex;font-family:"Roboto",Arial,sans-serif;font-size:17px;color:var(--muted);letter-spacing:.3px}
.main-nav a{color:inherit;text-decoration:none;display:block;height:52px;padding-top:3px}
.main-nav a.active{color:var(--brand);border-bottom:3px solid var(--brand)}

/* hero */
.hero{left:0;top:122px;width:1200px;height:520px;overflow:hidden}
.hero-photo{position:absolute;inset:0;background:linear-gradient(180deg,var(--placeholder-a) 0%,var(--placeholder-b) 100%)}
.hero-card{left:105px;top:131px;width:445px;height:200px;background:rgba(49,118,181,.92);border-radius:8px;padding:30px 40px}
.hero-card h1{font-family:"Roboto",Arial,sans-serif;font-weight:300;color:var(--white);font-size:31px;line-height:1.2}
.hero-card h1 span{display:block;font-size:39px}
.btn-outline{display:inline-block;margin-top:20px;width:150px;height:40px;border:2px solid var(--white);color:var(--white);font-family:"Roboto",Arial,sans-serif;font-weight:500;font-size:15px;text-align:center;line-height:36px;letter-spacing:.5px}
.dots{display:flex;gap:6px}
.dots i{display:block;width:18px;height:18px;border-radius:50%;background:var(--white);border:2px solid var(--white)}
.dots i.hollow{background:transparent}
.hero-dots{left:551px;top:435px}
.hero-wave{left:0;bottom:0}

/* who we are */
.who-photo{left:123px;top:608px;width:330px;height:330px;border-radius:50%;background:linear-gradient(180deg,var(--tile-a),var(--tile-b))}
.who-title{left:487px;top:655px;font-weight:300;font-size:38px;color:var(--ink)}
.who-text{left:489px;top:718px;width:580px;font-size:14.3px;line-height:27px;color:var(--muted)}
.btn-solid{left:489px;top:899px;width:136px;height:42px;background:linear-gradient(180deg,var(--brand) 0%,var(--brand-deep) 100%);border-radius:4px;color:var(--white);font-family:"Roboto",Arial,sans-serif;font-weight:500;font-size:13px;text-align:center;line-height:42px}

/* what we do */
.what{left:0;top:1011px;width:1200px;height:372px;background:linear-gradient(180deg,#3a7dba,#3176b5)}
.what-notch{left:570px;top:1011px}
.what-title{left:0;top:1080px;width:1200px;text-align:center;font-weight:300;font-size:34px;color:var(--white)}
.what-text{left:190px;top:1133px;width:820px;text-align:center;font-size:16.5px;line-height:26px;color:var(--white)}
.what-list{list-style:none;font-size:15px;font-weight:600;color:var(--white)}
.what-list li{height:36px;display:flex;align-items:center;gap:10px}
.what-list li::before{content:"";width:0;height:0;border-left:6px solid var(--brand-pale);border-top:5px solid transparent;border-bottom:5px solid transparent}

/* services */
.services-title{left:0;top:1426px;width:1200px;text-align:center;font-weight:300;font-size:33px;color:var(--ink)}
.service-card{top:1495px;width:240px;height:257px;border:1px solid var(--line);background:var(--white);text-align:center}
.service-photo{height:180px;background:linear-gradient(180deg,var(--tile-a),var(--tile-b))}
.service-card h3{font-family:"Roboto",Arial,sans-serif;font-weight:400;font-size:20px;color:var(--brand-deep);margin-top:10px}
.service-card p{font-size:12.5px;color:var(--muted);margin-top:4px}

/* testimonials */
.testimonials{left:0;top:1803px;width:1200px;height:349px;background:linear-gradient(90deg,#e8e8e8,#f2f2f2 50%,#e6e6e6)}
.testi-title{left:0;top:1858px;width:1200px;text-align:center;font-weight:300;font-size:32px;color:var(--ink)}
.testi-quote{left:205px;top:1920px;width:790px;text-align:center;font-style:italic;font-size:16px;line-height:29px;color:var(--muted)}
.quote-mark{font-family:Georgia,serif;font-size:70px;line-height:1;color:var(--muted);font-weight:700}
.testi-author{left:0;top:2000px;width:1200px;text-align:center;font-size:16px;color:var(--ink)}
.stars{left:547px;top:2035px;display:flex;gap:4px}
.testi-dots{left:563px;top:2088px}
.testi-dots i{width:15px;height:15px;background:var(--muted);border-color:var(--muted)}
.testi-dots i.hollow{background:transparent}

/* footer */
.site-footer{left:0;top:2152px;width:1200px;height:293px;background:var(--black);color:var(--white)}
.footer-brand{left:117px;top:2222px;display:flex;align-items:center;gap:12px}
.footer-brand .brand-dot{background:var(--line)}
.footer-brand .brand-name{color:var(--line)}
.footer-col{top:2200px;color:var(--white)}
.footer-col h4{font-family:"Roboto",Arial,sans-serif;font-weight:400;font-size:22px;margin-bottom:14px}
.footer-col li{list-style:none;font-size:13px;line-height:28px;color:#d8d8d8}
.socials{display:flex;gap:6px}
.socials i{display:block;width:32px;height:32px;border:2px solid var(--white);border-radius:50%}
.legal{left:0;top:2445px;width:1200px;height:65px;background:#6e6e6e;text-align:center;line-height:65px;font-size:12px;color:var(--line)}
</style>
</head>
<body>

<header class="site-header abs">
  <div class="brand abs"><span class="brand-dot"></span><span class="brand-name">Bright Morrow Ltd</span></div>
  <div class="phone abs">
    <svg width="20" height="20" viewBox="0 0 24 24" aria-hidden="true"><path fill="#0455a3" d="M6.6 10.8a15.1 15.1 0 0 0 6.6 6.6l2.2-2.2c.3-.3.7-.4 1-.2 1.1.4 2.3.6 3.6.6.6 0 1 .4 1 1V20c0 .6-.4 1-1 1A17 17 0 0 1 3 4c0-.6.4-1 1-1h3.5c.6 0 1 .4 1 1 0 1.3.2 2.5.6 3.6.1.3 0 .7-.2 1z"/></svg>
    01925 555 0148
  </div>
  <nav class="main-nav abs">
    <a class="active" href="#" style="width:48px;margin-right:55px">HOME</a>
    <a href="#" style="margin-right:61px">ABOUT US</a>
    <a href="#" style="margin-right:60px">SERVICES</a>
    <a href="#" style="margin-right:52px">GALLERY</a>
    <a href="#" style="margin-right:52px">BLOG</a>
    <a href="#">CONTACT</a>
  </nav>
</header>

<section class="hero abs">
  <div class="hero-photo" role="img" aria-label="Photo of a bright, freshly cleaned empty room"></div>
  <div class="hero-card abs">
    <h1>Domestic and Commercial <span>Cleaning Services</span></h1>
    <a class="btn-outline">HIRE US</a>
  </div>
  <div class="dots hero-dots abs"><i class="hollow"></i><i></i><i></i><i></i></div>
  <svg class="hero-wave abs" width="1200" height="110" viewBox="0 0 1200 110" aria-hidden="true">
    <path d="M0 110 V60 C300 10 500 50 750 80 C950 100 1100 70 1200 20 V110 Z" fill="#d4d4d4"/>
    <path d="M0 110 V82 C300 20 520 60 760 88 C960 108 1100 80 1200 40 V110 Z" fill="#ffffff"/>
  </svg>
</section>

<section class="who">
  <div class="who-photo abs" role="img" aria-label="Photo of a bright white bedroom"></div>
  <h2 class="who-title abs head-font">Who we are</h2>
  <p class="who-text abs">Morbi porta libero id ullamcorper nonummy nibh ligula pulvinar metus eget consectetuer augue nisi quis lacus Ut ac mi quis lacus mollis aliquam Curabitur iaculis tempus eros Curabitur vel mi sit amet magna malesuada<br>Ut nisi erat fermentum vel congue id euismod in elit Fusce ultricies orci ac feugiat suscipit leo massa sodales velit et scelerisque mi tortor at ipsum cligula augue bibendum accumsan vestibulum ut commodo a mi Morbi ornare</p>
  <a class="btn-solid abs">READ MORE</a>
</section>

<section class="what abs" role="img" aria-label="Living room photo behind a blue tint"></section>
<svg class="what-notch abs" width="60" height="30" viewBox="0 0 60 30" aria-hidden="true"><path d="M0 0 H60 L30 28 Z" fill="#ffffff"/></svg>
<h2 class="what-title abs head-font">What we do</h2>
<p class="what-text abs">Morbi porta libero id ullamcorper nonummy nibh ligula pulvinar metus eget consectetuer augue nisi quis lacus Ut ac mi quis lacus mollis aliquam Curabitur iaculis tempus eros</p>
<ul class="what-list abs" style="left:213px;top:1211px"><li>Magna malesuada nisi</li><li>Erat fermentum vel congue</li></ul>
<ul class="what-list abs" style="left:502px;top:1211px"><li>Euismod in elit</li><li>Fusce ultricies orci ac feugiat</li></ul>
<ul class="what-list abs" style="left:823px;top:1211px"><li>Suscipit leo massa</li><li>Aodales velit et</li></ul>

<section class="services">
  <h2 class="services-title abs head-font">Our Services</h2>
  <article class="service-card abs" style="left:100px">
    <div class="service-photo" role="img" aria-label="Photo of a clean kitchen"></div>
    <h3>House Cleaning</h3><p>Morbi porta libero ullamcorper</p>
  </article>
  <article class="service-card abs" style="left:353px">
    <div class="service-photo" role="img" aria-label="Photo of a tidy office"></div>
    <h3>Office Cleaning</h3><p>Morbi porta libero ullamcorper</p>
  </article>
  <article class="service-card abs" style="left:606px">
    <div class="service-photo" role="img" aria-label="Photo of a polished building floor"></div>
    <h3>Building Floor</h3><p>Morbi porta libero ullamcorper</p>
  </article>
  <article class="service-card abs" style="left:859px">
    <div class="service-photo" role="img" aria-label="Photo of clean office furniture"></div>
    <h3>Furniture Cleaning</h3><p>Morbi porta libero ullamcorper</p>
  </article>
</section>

<section class="testimonials abs" role="img" aria-label="Faded living room photo"></section>
<h2 class="testi-title abs head-font">Testimonials</h2>
<span class="quote-mark abs" style="left:163px;top:1910px">&ldquo;</span>
<span class="quote-mark abs" style="left:993px;top:1910px">&rdquo;</span>
<p class="testi-quote abs">Commodo a mi Morbi ornare gravida elit Integer congue augue et malesuada iaculis ipsum dui aliquet<br>felis at cursus magna nisl nec elit Praesent elementum elit at tellus nec ultricies</p>
<p class="testi-author abs">By Author Name</p>
<div class="stars abs">
  <svg width="104" height="24" viewBox="0 0 104 24" aria-label="Four stars">
    <g fill="#f5a623">
      <path id="star" d="M12 1l3.2 7 7.6.7-5.8 5 1.8 7.4L12 17.2 5.2 21.1 7 13.7 1.2 8.7 8.8 8z"/>
      <use href="#star" x="27"/><use href="#star" x="54"/><use href="#star" x="81"/>
    </g>
  </svg>
</div>
<div class="dots testi-dots abs"><i class="hollow"></i><i></i><i></i><i></i></div>

<footer class="site-footer abs"></footer>
<div class="footer-brand abs"><span class="brand-dot"></span><span class="brand-name">Bright Morrow Ltd</span></div>
<div class="footer-col abs" style="left:343px"><h4>Quick Links</h4><ul><li>About Us</li><li>Our Services</li><li>Our Gallery</li><li>Blogs</li></ul></div>
<div class="footer-col abs" style="left:520px"><h4>Resources</h4><ul><li>Term of Use</li><li>Privacy Policy</li><li>FAQ</li><li>Contact</li></ul></div>
<div class="footer-col abs" style="left:700px"><h4>Contact Info</h4><ul><li>14 Cairo Street Unit 3</li><li>Warrington, WA1 1EH</li><li>(01925) 555 0172</li><li>hello@brightmorrow.example</li></ul></div>
<div class="footer-col abs" style="left:951px"><h4>Follow Us</h4><div class="socials"><i></i><i></i><i></i><i></i></div></div>
<div class="legal abs">© 2016 Company Name &nbsp;All right reserved &nbsp;Term of Use</div>

</body>
</html>
```